Copper Moth Bar & Grill Takeout Menu

Please create a takeout menu using the attached dine-in menu.
Take out menu size: Tri-Fold 11x17

Industry/Entity Type

Bar & Grill (Restaurant)

Colors

Designer to choose colors to be used in the design.

Requirements
Must have
• Phone number and website. "Order Online" "Order for Delivery"
Nice to have
• Area on the back of the menu to feature happy hour specials.

```html
<!DOCTYPE html>
<html lang="en">
<head>
<meta charset="utf-8">
<title>Copper Moth Bar &amp; Grill – Takeout Menu</title>
<link href="https://fonts.googleapis.com/css2?family=Anton&family=Cinzel:wght@600;700&family=Cormorant+Garamond:ital,wght@1,500&family=Fredoka:wght@500;600&family=Montserrat:wght@400;500;600;700&display=swap" rel="stylesheet">
<style>
:root{
  --ink:#121212;
  --paper:#efefed;
  --card:#f7f7f5;
  --cyan:#5cd4df;
  --yellow:#fcd657;
  --blue:#2d62b3;
  --grey:#4a4a4a;
  --stage:#d9d9d9;
}
*{box-sizing:border-box;margin:0;padding:0}
html,body{width:1200px;height:2660px;overflow:hidden}
body{background:var(--stage);font-family:"Montserrat",sans-serif;color:var(--ink)}
.spread{position:absolute;left:50px;width:1100px;height:712px;display:flex;
  background:radial-gradient(circle at 30% 20%,#f6f6f4,var(--paper) 70%);box-shadow:0 10px 30px rgba(0,0,0,.25)}
.spread.inside{top:568px}
.spread.outside{top:1380px}
.panel{width:33.333%;height:100%;padding:16px}
.frame{height:100%;border:1.4px solid #3a3a3a;border-radius:14px;outline:3px dotted #a8a8a8;outline-offset:5px;
  background:var(--card);padding:16px 18px;overflow:hidden;display:flex;flex-direction:column}
.banner{align-self:center;background:var(--ink);color:#fff;font:700 13px "Cinzel",serif;letter-spacing:.5px;
  padding:3px 26px;margin:4px 0 8px;clip-path:polygon(0 0,100% 0,95% 50%,100% 100%,0 100%,5% 50%)}
.banner.wide{padding:3px 40px}
.note{font-size:7.6px;line-height:1.25;color:var(--grey);margin-bottom:6px}
.note.center{text-align:center}
.item{display:grid;grid-template-columns:1fr auto;column-gap:10px;margin-bottom:6px;align-items:start}
.item h4{font-size:9.2px;font-weight:600}
.item p{font-size:7.4px;line-height:1.22;color:var(--grey)}
.price{background:var(--yellow);font:700 11px "Montserrat",sans-serif;padding:2px 4px;min-width:24px;text-align:center;white-space:nowrap}
.price sup{font-size:6px}
.plain{font-weight:600;font-size:10px;white-space:nowrap}
.list{font-size:8px;text-align:center;line-height:1.35;color:var(--grey);margin-bottom:6px}
.veg{width:10px;height:10px;vertical-align:-1px;margin-left:3px}
.cyan-box{background:var(--cyan);padding:8px 18px 10px;margin:2px -4px 8px}
.cyan-box .banner{margin-top:-14px}
.row{display:flex;justify-content:space-between;align-items:center;font-size:9.4px;font-weight:500;margin:5px 0}
.site{font:700 15px "Montserrat",sans-serif;text-align:center;margin-top:auto;letter-spacing:.3px}
/* happy hour */
.happy{text-align:center;margin:8px 0 10px}
.happy .sunday{display:inline-block;background:var(--yellow);font:600 17px "Fredoka",sans-serif;line-height:1;padding:4px 14px 2px}
.happy .sunday small{display:block;font-size:11px}
.happy .hh{background:var(--ink);color:#fff;font:600 28px "Fredoka",sans-serif;border-radius:22px;padding:2px 0;margin:0 -6px}
.happy .spec{display:inline-block;background:var(--yellow);font:700 24px "Cinzel",serif;padding:2px 16px;border-radius:0 0 10px 10px}
.order{text-align:center}
.order .ico{width:30px;height:30px;display:block;margin:6px auto 3px}
.order .label{font:500 16px "Montserrat",sans-serif}
.order .phone{font:700 20px "Montserrat",sans-serif}
/* cover */
.cover{align-items:center;text-align:center}
.brand{font:600 38px/1.05 "Fredoka",sans-serif;color:var(--ink);margin:22px 0 18px}
.food{position:relative;width:250px;height:70px}
.food svg{position:absolute;inset:0}
.food span{position:relative;font:600 42px/70px "Fredoka",sans-serif;letter-spacing:3px}
.menu-word{font:96px/1 "Anton",sans-serif;margin-top:-4px}
.delivery{position:relative;width:290px;height:140px;margin-top:30px}
.delivery svg{position:absolute;inset:0}
.delivery span{position:relative;display:block;font:36px/1 "Anton",sans-serif;padding-top:38px}
.badge{width:40px;height:40px;margin-top:14px}
/* columns */
.duo{display:grid;grid-template-columns:1fr auto 1fr auto;column-gap:6px;row-gap:5px;align-items:center;margin-bottom:6px;font-size:8px;font-weight:500}
.duo .price{font-size:10px}
.soup-size{font:700 11px "Anton",sans-serif;letter-spacing:.5px;white-space:nowrap}
.burger{display:grid;grid-template-columns:1fr 34px 34px 34px;column-gap:4px;margin-bottom:4px;align-items:start}
.burger .price{font-size:8.6px;min-width:0;padding:2px 1px}
.burger h4{font-size:8.6px;font-weight:600}
.burger p{font-size:7px;line-height:1.2;color:var(--grey)}
.prot{width:26px;height:26px;border:1.5px solid var(--ink);border-radius:50%;justify-self:center;background:#fff}
.legal{font:500 italic 11px/1.2 "Cormorant Garamond",serif;text-align:center;margin-top:auto}
.legend{font:500 italic 14px "Cormorant Garamond",serif;text-align:center;margin-top:6px}
</style>
</head>
<body>
<svg width="0" height="0" style="position:absolute" aria-hidden="true">
  <symbol id="leaf" viewBox="0 0 12 12"><path d="M6 11 C5 7 3 4 1 2 M6 11 C7 6 9 3 11 1 M6 7 C8 6 9 4 11 1" fill="none" stroke="#121212" stroke-width="1.4"/></symbol>
</svg>

<!-- INSIDE SPREAD -->
<section class="spread inside">
  <div class="panel"><div class="frame">
    <h2 class="banner wide">OTHER HANDHELDS</h2>
    <p class="note center"><b>All served with Hand Cut Fries or Sweet Potato Fries. Premium sides available for an up charge +2</b></p>
    <div class="item"><div><h4>Cat Club</h4><p>Sliced whole wheat bread with roasted garlic aioli, grilled marinated chicken breast, provolone cheese, bacon, lettuce and tomato.</p></div><span class="price"><sup>$</sup>15</span></div>
    <div class="item"><div><h4>Southwest Melt</h4><p>Sliced whole wheat bread with roasted garlic aioli, 3 pepper colby jack, roasted red peppers and corn.</p></div><span class="price"><sup>$</sup>14</span></div>
    <div class="item"><div><h4>What's Gouda?</h4><p>Sliced whole wheat bread with roasted garlic aioli, smoked gouda and provolone cheeses, roasted red peppers and portobello mushrooms.</p></div><span class="price"><sup>$</sup>14</span></div>
    <div class="item"><div><h4>Westover Melt</h4><p>Sliced whole wheat bread with roasted garlic aioli, zucchini, portobello mushrooms, red peppers, with melted brie and provolone cheeses.</p></div><span class="price"><sup>$</sup>14</span></div>
    <h2 class="banner">CHEESES</h2>
    <p class="list">Vermont Cheddar | Smoked Gouda 3-Pepper Colby Jack<br>Monterey Jack | Swiss | Brie Provolone | American</p>
    <h2 class="banner">CONDIMENTS:</h2>
    <p class="list">Horseradish Aioli | Chipotle Crema | Roasted Garlic Aioli | Citrus Aioli<br>Spicy Ketchup | Dijon Mustard | Yellow Mustard | Mayo | Ketchup</p>
    <h2 class="banner">TOPPINGS</h2>
    <p class="list">Bacon | Shrimp | Egg | Red Onion | White Onion | Portobello Mushrooms | Roasted Corn | Roasted Red Peppers Guacamole | Pico De Gallo | Fresh or Pickled Jalapenos</p>
    <div class="cyan-box">
      <h2 class="banner">SIDES</h2>
      <div class="row"><span>Potato Salad</span><span class="price"><sup>$</sup>4</span></div>
      <div class="row"><span>Fire Roasted Veggies</span><span class="price"><sup>$</sup>6</span></div>
      <div class="row"><span>Brown Rice, Quinoa, &amp; Kale Medley</span><span class="price"><sup>$</sup>8</span></div>
    </div>
    <p class="site">WWW.COPPERMOTHGRILL.COM</p>
  </div></div>

  <div class="panel"><div class="frame">
    <div class="cyan-box" style="margin-top:4px">
      <h2 class="banner wide">KIDS MENU</h2>
      <p class="note center" style="color:var(--ink);font-size:8.4px">All served with French Fries</p>
      <div class="row"><span>Grilled Cheese <svg class="veg"><use href="#leaf"/></svg></span><span class="price"><sup>$</sup>8</span></div>
      <div class="row"><span>Cheese Quesadilla <svg class="veg"><use href="#leaf"/></svg></span><span class="price"><sup>$</sup>8</span></div>
      <div class="row"><span>Mac &amp; Cheese <svg class="veg"><use href="#leaf"/></svg></span><span class="price"><sup>$</sup>8</span></div>
      <div class="row"><span>Chicken Tenders</span><span class="price"><sup>$</sup>10</span></div>
    </div>
    <div class="happy">
      <div class="sunday">EVERY SUNDAY<small>START FROM 7PM-11 PM</small></div>
      <div class="hh">HAPPY HOUR</div>
      <div class="spec">SPECIALS</div>
    </div>
    <div class="order">
      <svg class="ico" viewBox="0 0 30 30" aria-hidden="true"><circle cx="15" cy="15" r="15" fill="var(--blue)"/><rect x="10" y="7" width="10" height="16" rx="1.5" fill="none" stroke="#fff" stroke-width="1.8"/><path d="M13 15l2 2 3-4" stroke="#fff" stroke-width="1.6" fill="none"/></svg>
      <p class="label">ORDER ONLINE</p>
      <svg class="ico" viewBox="0 0 30 30" aria-hidden="true"><circle cx="15" cy="15" r="15" fill="var(--blue)"/><circle cx="9" cy="20" r="3" fill="#fff"/><circle cx="21" cy="20" r="3" fill="#fff"/><path d="M9 17h9l3-6M12 11h6v6h-6z" stroke="#fff" stroke-width="1.8" fill="none"/></svg>
      <p class="label">ORDER FOR DELIVERY</p>
      <svg class="ico" viewBox="0 0 30 30" aria-hidden="true"><circle cx="15" cy="15" r="15" fill="var(--ink)"/><path d="M10 8c-2 2-1 6 3 10s8 5 10 3l-3-3-2 1c-2-1-4-3-5-5l1-2z" fill="#fff"/></svg>
      <p class="phone">555-014-2290</p>
      <svg class="ico" viewBox="0 0 30 30" aria-hidden="true"><circle cx="15" cy="15" r="15" fill="var(--ink)"/><circle cx="15" cy="15" r="8" fill="none" stroke="#fff" stroke-width="1.5"/><ellipse cx="15" cy="15" rx="3.5" ry="8" fill="none" stroke="#fff" stroke-width="1.3"/><path d="M7 15h16" stroke="#fff" stroke-width="1.3"/></svg>
    </div>
    <p class="site">WWW.COPPERMOTHGRILL.COM</p>
  </div></div>

  <div class="panel"><div class="frame cover">
    <p class="brand">Copper Moth<br>Bar &amp; Grill</p>
    <div class="food">
      <svg viewBox="0 0 250 70" aria-hidden="true"><path d="M0 22 L34 14 L34 60 L0 66 L14 42Z M250 22 L216 14 L216 60 L250 66 L236 42Z" fill="#3fb3bf"/><path d="M22 8 Q125 -6 228 8 L228 58 Q125 44 22 58Z" fill="var(--cyan)"/></svg>
      <span>FOOD</span>
    </div>
    <p class="menu-word">MENU</p>
    <svg class="badge" viewBox="0 0 30 30" aria-hidden="true"><circle cx="15" cy="15" r="15" fill="var(--blue)"/><circle cx="9" cy="20" r="3" fill="#fff"/><circle cx="21" cy="20" r="3" fill="#fff"/><path d="M9 17h9l3-6M12 11h6v6h-6z" stroke="#fff" stroke-width="1.8" fill="none"/></svg>
    <div class="delivery" style="margin-top:0">
      <svg viewBox="0 0 290 140" aria-hidden="true"><path d="M0 70 L145 0 L290 70 L145 140Z" fill="var(--yellow)"/></svg>
      <span>ORDER<br>DELIVERY</span>
    </div>
    <p class="site">WWW.COPPERMOTHGRILL.COM</p>
  </div></div>
</section>

<!-- OUTSIDE SPREAD -->
<section class="spread outside">
  <div class="panel"><div class="frame">
    <h2 class="banner wide">SALAD</h2>
    <div class="item"><div><h4>Combo Cat</h4><p>Enjoy a side House and a cup of any soup.</p></div><span class="price"><sup>$</sup>11</span></div>
    <div class="item"><div><h4>Cat House Salad <svg class="veg"><use href="#leaf"/></svg></h4><p>Spring lettuce mix, fresh red peppers, onion, cherry tomatoes, cucumber, and croutons. Served with Red Wine Vinaigrette.</p></div><span class="price"><sup>$</sup>11</span></div>
    <div class="item"><div><h4>Grilled Chicken Salad</h4><p>Spring lettuce mix, grilled chicken breast, bacon, fresh red peppers, onions, tomatoes, cucumber and feta cheese. Served with Red Wine Vinaigrette</p></div><span class="price"><sup>$</sup>15</span></div>
    <div class="item"><div><h4>Grilled Shrimp Salad*</h4><p>Spring lettuce mix, garlic Roasted Shrimp, roasted corn, pico de gallo fresh avocado. Served with Lemon Champagne Vinaigrette</p></div><span class="price"><sup>$</sup>16</span></div>
    <div class="item"><div><h4>Goat Cheese Salad <svg class="veg"><use href="#leaf"/></svg></h4><p>Spring lettuce mix, fried goat cheese, fresh red peppers, cranberries, white onions, and cherry tomatoes. Served with Lemon Champagne Vinaigrette.</p></div><span class="price"><sup>$</sup>14</span></div>
    <div class="item"><div><h4>The Skinny Cat <svg class="veg"><use href="#leaf"/></svg></h4><p>Spring lettuce mix, sliced apple, sun dried cranberries, roasted corn, cherry tomatoes, and feta cheese. Served with Balsamic Vinaigrette.</p></div><span class="price"><sup>$</sup>14</span></div>
    <div class="item"><div><h4>Small House Salad <svg class="veg"><use href="#leaf"/></svg></h4></div><span class="price"><sup>$</sup>6</span></div>
    <p style="font-size:8.4px;font-weight:600;margin-top:4px">Add:<br>Grilled Chicken 5 | Garlic Roasted Shrimp 5 Fried Goat Cheese 4</p>
    <div class="cyan-box" style="margin-top:18px">
      <h2 class="banner wide">DRESSINGS</h2>
      <p class="list" style="color:var(--ink);font-weight:600;font-size:8.6px">Balsamic Vinaigrette | Caesar<br>Red Wine Vinaigrette | Honey-Mustard | Lemon<br>Champagne Vinaigrette | Ranch | Blue Cheese</p>
    </div>
    <p class="legal">*The consumption of raw or undercooked eggs, meat, poultry, seafood or shellfish may contribute to food borne illness, especially if you have a medical condition.</p>
    <p class="legend"><svg class="veg" style="width:14px;height:14px"><use href="#leaf"/></svg> Vegetarian &nbsp;<svg width="12" height="14" viewBox="0 0 12 14" aria-hidden="true"><path d="M9 1c-1 5-4 9-8 12 4 0 9-4 9-10z" fill="var(--ink)"/></svg> - Spicy</p>
  </div></div>

  <div class="panel"><div class="frame">
    <h2 class="banner wide">TORTILLA CHIPS</h2>
    <div class="duo">
      <span>with House-made Salsa Verde</span><span class="price"><sup>$</sup>7</span><span>With Queso</span><span class="price"><sup>$</sup>8</span>
      <span>with House-made Fire Roasted Salsa</span><span class="price"><sup>$</sup>7</span><span>With Chili con Queso</span><span class="price"><sup>$</sup>9</span>
      <span>with Guacamole &amp; Pico De Gallo</span><span class="price"><sup>$</sup>8</span><span></span><span></span>
    </div>
    <h2 class="banner">WINGS</h2>
    <div class="item"><div><h4>8 pieces</h4><p>Flash-fried to a crispy golden brown and tossed in your choice of sauce. Choose from our Signature Hot, or Mild Sauce, or BBQ. Your choice of ranch or blue cheese.</p></div><span class="price"><sup>$</sup>14</span></div>
    <h2 class="banner">QUESADILLAS</h2>
    <div class="duo">
      <span>Cheddar and Monterey Jack Cheese</span><span class="price"><sup>$</sup>12</span><span>Fire Roasted Vegetables &amp; Cheese</span><span class="price"><sup>$</sup>14</span>
      <span>Pulled Marinated Chicken &amp; Cheese</span><span class="price"><sup>$</sup>16</span><span>Garlic Roasted Shrimp &amp; Cheese</span><span class="price"><sup>$</sup>16</span>
    </div>
    <p class="note">All quesadillas are stuffed with roasted red peppers, black beans and your choice below. Served with guacamole, pico de gallo, and chipotle crema on the side.</p>
    <h2 class="banner wide">CLAW-FULL NACHOS</h2>
    <p class="note">Tortilla chips, melted white queso, Cheddar and Monterey Jack cheeses, pico de gallo, guacamole, chipotle sourcream, jalapenos, black beans, &amp; green onions</p>
    <div class="duo">
      <span>Copper Moth Chili Nachos</span><span class="price"><sup>$</sup>14</span><span>Garlic Roasted Shrimp</span><span class="price"><sup>$</sup>16</span>
      <span>Pulled Chicken Nachos</span><span class="price"><sup>$</sup>16</span><span>Fire Roasted Vegetables Nachos</span><span class="price"><sup>$</sup>14</span>
    </div>
    <h2 class="banner wide">FRENCH FRIES</h2>
    <p class="note">Served with our house made Garlic Aioli and Spicy Ketchup.</p>
    <div class="duo">
      <span>Fries Only <svg class="veg"><use href="#leaf"/></svg></span><span class="price"><sup>$</sup>7</span><span>Cheddar-Jack <svg class="veg"><use href="#leaf"/></svg> Cheese Fries</span><span class="price"><sup>$</sup>8</span>
      <span>Sweet Potato Fries <svg class="veg"><use href="#leaf"/></svg></span><span class="price"><sup>$</sup>7</span><span>Cheddar-Jack Cheese, Bacon Fries</span><span class="price"><sup>$</sup>9</span>
    </div>
    <div class="item"><div><h4>Chili Cheese Fries</h4><p>Topped with Copper Moth Chili, cheddar jack cheese and served with chipotle crema on the side.</p></div><span class="price"><sup>$</sup>10</span></div>
  </div></div>

  <div class="panel"><div class="frame">
    <h2 class="banner wide">SOUPS &amp; BOWLS</h2>
    <div class="item"><div><h4>Copper Moth Chili</h4><p>Copper Moth Signature Chili with lean ground beef, black beans, and corn. Topped with cheddar cheese and greenonion, served with tri-color tortilla chips.</p></div><span class="soup-size">CUP 6 | BOWL 8</span></div>
    <div class="item"><div><h4>Southwestern Sweet Potato Soup <svg class="veg"><use href="#leaf"/></svg></h4><p>A delicious mix of sweet potatoes, corn, bell peppers, and black beans, this vegan soup delivers top flavor and quality with every bowl. Served with tri-color tortilla chips.</p></div><span class="soup-size">CUP 6 | BOWL 8</span></div>
    <div class="item"><div><h4>Ancient Grains Bowl</h4><p>Quinoa, brown rice, kale and fresh spinach, with fire roasted portobello mushrooms, zucchini and red peppers. Topped with fresh avocado, and feta cheese. Served with Lemon Champagne Vinaigrette</p></div><span class="price"><sup>$</sup>12</span></div>
    <p style="font-size:8px;font-weight:600;margin-bottom:4px">Add: Grilled Chicken 5 | Garlic Roasted Shrimp 5</p>
    <h2 class="banner" style="text-align:center;line-height:1.1">GOURMET BURGERS &amp;<br>SANDWICHES</h2>
    <p class="note">Start with your style and then choose your protein. Our burgers are house made and cooked to your temperature. Our fresh grilled chicken breast is marinated in house and cooked to perfection. Keep it vegetarian by choosing a vegetarian style along with the Quinoa Lentil Burger. All are served on a potato bun with lettuce, tomato, onion and your choice of hand cut fries or sweet potato fries.</p>
    <p style="font-size:7.6px;font-weight:700;margin-bottom:3px">Premium sides available for an up charge + $2</p>
    <div class="burger" style="align-items:center"><h4>Gluten-Free Bun Available Upon Request + $2</h4>
      <span class="prot" role="img" aria-label="Beef patty icon"></span><span class="prot" role="img" aria-label="Chicken icon"></span><span class="prot" role="img" aria-label="Vegetarian patty icon"></span></div>
    <div class="burger"><div><h4>Calico Cat <svg class="veg"><use href="#leaf"/></svg></h4><p>Roasted red peppers, red onions, brie cheese, and horseradish aioli.</p></div><span class="price"><sup>$</sup>15.00*</span><span class="price"><sup>$</sup>14.00</span><span class="price"><sup>$</sup>13.00</span></div>
    <div class="burger"><div><h4>Tiger Cat <svg class="veg"><use href="#leaf"/></svg></h4><p>Cheddar, Monterey Jack, and Provolone</p></div><span class="price"><sup>$</sup>15.00*</span><span class="price"><sup>$</sup>14.00</span><span class="price"><sup>$</sup>13.50</span></div>
    <div class="burger"><div><h4>Cat Scratch Fever <svg class="veg"><use href="#leaf"/></svg></h4><p>Guacamole, 3 pepper colby jack, pico de gallo, and chipotle mayo</p></div><span class="price"><sup>$</sup>15.50*</span><span class="price"><sup>$</sup>14.50</span><span class="price"><sup>$</sup>14.00</span></div>
    <div class="burger"><div><h4>The Fat Cat</h4><p>Fried egg*, bacon, cheddar cheese, and garlic aioli</p></div><span class="price"><sup>$</sup>16.00*</span><span class="price"><sup>$</sup>15.00</span><span class="price"><sup>$</sup>14.50</span></div>
    <div class="burger"><div><h4>Tabby Cat <svg class="veg"><use href="#leaf"/></svg></h4><p>Melted brie cheese, sliced apple, and citrus aioli</p></div><span class="price"><sup>$</sup>16.50*</span><span class="price"><sup>$</sup>15.50</span><span class="price"><sup>$</sup>14.50</span></div>
    <div class="burger"><div><h4>The Sphynx <svg class="veg"><use href="#leaf"/></svg></h4><p>Portobello mushrooms, roasted red peppers, smoked gouda cheese, and roasted garlic aioli</p></div><span class="price"><sup>$</sup>16.50*</span><span class="price"><sup>$</sup>15.50</span><span class="price"><sup>$</sup>14.50</span></div>
    <div class="burger"><div><h4>Maine Coon</h4><p>Grilled shrimp*, roasted corn, swiss cheese, and roasted garlic aioli</p></div><span class="price"><sup>$</sup>16.50*</span><span class="price"><sup>$</sup>15.50</span><span class="price"><sup>$</sup>14.50</span></div>
    <div class="burger"><div><h4>Alley Cat <svg class="veg"><use href="#leaf"/></svg></h4><p>Whats up your alley? Choose a cheese, condiment and one topping. Additional Toppings $1 | Bacon, Egg, Shrimp - $2</p></div><span class="price"><sup>$</sup>14.00*</span><span class="price"><sup>$</sup>13.00</span><span class="price"><sup>$</sup>12.00</span></div>
  </div></div>
</section>
</body>
</html>
```